Product label for herbal salves, lotions, soaps and tinctures

We need a very simple, clean and organic looking label that can be used for an ointment jar, a lotion bottle and a dropper bottle.
We have an existing logo (see attached). We like the colors white, olive green, gold and black. It needs to include product name as dominant and logo. It also needs to include an ingredient list, and usage statement. Include weight of product, distributed by, made in the USA, and QVX statement.
Example of what needs to be present:
Logo
Name: Tranquil Ease Blend
Used for: For Muscle Aches, Arthritis, Tendonitis, Headaches
To Use: For muscle aches, arthritis and tendonitis, massage into affected area. For tension headache apply to neck, temples and forehead.
Store in a cool and dry place, away from direct heat and sunlight.
Weight of product: 1.75
DIST. BY: Copper Brook Herbal
Made in the USA
This product is not intended to diagnose, treat, cure
or prevent any disease. Not regulated
by the QVX. Please consult your health care practitioner
before using product. Discontinue use if any adverse reaction occurs.
Ingredient list:
Wildcrafted Ingredients:
Ashwagandha Root, Peppermint Leaf, Hops Flowers, St. John’s Wort Herb, Arnica Flowers, Green Tea Leaf, Alfalfa Leaf, Dandelion Root, Burdock Root, Chickweed Herb, Chaparral Leaf, Yarrow Flowers, Boneset Herb, Moringa Leaf, Meadowsweet Herb, Nettle Leaf
Organic Ingredients:
Olive Oil, Aloe Leaf, Sweet Birch Bark, Helichrysum Flowers, Holy Basil Leaf, Borage Herb, Ginger Root, Angelica Root, White Willow Bark, Mustard Seed, Beeswax, Vitamin E, Essential Oils
Dimensions of Jar:
Circumference: 7 in.
Height: 1 in.

```html
<!DOCTYPE html>
<html lang="en">
<head>
<meta charset="utf-8">
<title>Tranquil Ease Blend – Jar Label</title>
<link href="https://fonts.googleapis.com/css2?family=Quicksand:wght@400;500;700&family=Didact+Gothic&display=swap" rel="stylesheet">
<style>
  :root {
    --paper: #ffffff;
    --page: #f3f3f1;
    --ink: #1a1a1a;
    --olive: #6b6a22;
    --gold: #d59a2b;
    --grey-name: #6e6e6e;
    --rule: #2a2a2a;
    --sprig: #e9e9e6;
  }
  html, body {
    margin: 0;
    padding: 0;
    width: 1200px;
    height: 810px;
    overflow: hidden;
    background: var(--page);
  }
  .canvas {
    position: relative;
    width: 1200px;
    height: 810px;
  }
  .label {
    position: absolute;
    left: 20px;
    top: 323px;
    width: 1158px;
    height: 164px;
    background: var(--paper);
    border: 1px solid var(--rule);
    font-family: "Didact Gothic", sans-serif;
    color: var(--ink);
  }
  .panel-usage {
    position: absolute;
    left: 22px;
    top: 14px;
    width: 345px;
    text-align: center;
    font-size: 7.4px;
    line-height: 14px;
  }
  .panel-usage .directions {
    font-size: 9.4px;
    line-height: 14.5px;
    margin: 0 0 12px;
  }
  .panel-usage p { margin: 0; }
  .panel-brand {
    position: absolute;
    left: 425px;
    top: 0;
    width: 320px;
    height: 164px;
    text-align: center;
  }
  .sprig {
    position: absolute;
    background: linear-gradient(135deg, var(--sprig), rgba(233,233,230,0));
    border-radius: 40% 60% 50% 50%;
  }
  .sprig-left { left: 15px; top: 0; width: 100px; height: 62px; }
  .sprig-right { right: 15px; top: 0; width: 110px; height: 72px; }
  .brand-name {
    position: relative;
    margin-top: 40px;
    font-family: "Quicksand", sans-serif;
    font-weight: 700;
    font-size: 22px;
    color: var(--olive);
    line-height: 26px;
  }
  .product-name {
    position: relative;
    margin: 16px auto 0;
    width: 232px;
    font-family: "Quicksand", sans-serif;
    font-weight: 500;
    font-size: 22px;
    color: var(--grey-name);
    padding-bottom: 4px;
    border-bottom: 1.5px solid var(--gold);
    white-space: nowrap;
  }
  .used-for {
    margin-top: 4px;
    font-family: "Quicksand", sans-serif;
    font-weight: 700;
    font-size: 7.6px;
    color: var(--olive);
  }
  .panel-ingredients {
    position: absolute;
    left: 785px;
    top: 24px;
    width: 350px;
    text-align: center;
    font-size: 7.2px;
    line-height: 15px;
  }
  .panel-ingredients h2,
  .panel-ingredients h3 {
    margin: 0;
    font-weight: 400;
    font-size: 9.2px;
    line-height: 15px;
  }
  .panel-ingredients h2 { color: var(--gold); }
  .panel-ingredients h3 { color: var(--olive); }
  .panel-ingredients p { margin: 0; }
</style>
</head>
<body>
<div class="canvas">
  <section class="label">
    <div class="panel-usage">
      <p class="directions">For muscle aches, arthritis and tendonitis, massage into affected area.<br>For tension headache apply to neck, temples and forehead.</p>
      <p>Store in a cool and dry place, away from direct heat and sunlight.</p>
      <p>Weight of product: 1.75</p>
      <p>DIST. BY: Copper Brook Herbal</p>
      <p>MADE IN THE USA</p>
      <p>This product is not intended to diagnose, treat, cure&nbsp; or prevent any disease.</p>
      <p>Not regulated by the QVX. Please consult your health care practitioner</p>
      <p>before using product. Discontinue use if any adverse reaction occurs.</p>
    </div>

    <div class="panel-brand">
      <div class="sprig sprig-left" role="img" aria-label="Faint line drawing of an olive branch"></div>
      <div class="sprig sprig-right" role="img" aria-label="Faint line drawing of an olive branch with fruit"></div>
      <div class="brand-name">Copper Brook Herbal</div>
      <div class="product-name">Tranquil Ease Blend</div>
      <div class="used-for">For Muscle Aches, Arthritis, Tendonitis, Headaches</div>
    </div>

    <div class="panel-ingredients">
      <h2>INGREDIENT LIST :</h2>
      <h3>Wildcrafted Ingredients:</h3>
      <p>Ashwagandha Root, Peppermint Leaf, Hops Flowers, St. John’s Wort Herb, Arnica Flowers, Green Tea Leaf, Alfalfa Leaf, Dandelion Root, Burdock Root, Chickweed Herb, Chaparral Leaf, Yarrow Flowers, Boneset Herb, Moringa Leaf, Meadowsweet Herb, Nettle Leaf</p>
      <h3>Organic Ingredients:</h3>
      <p>Olive Oil, Aloe Leaf, Sweet Birch Bark, Helichrysum Flowers, Holy Basil Leaf, Borage Herb, Ginger Root, Angelica Root, White Willow Bark, Mustard Seed, Beeswax, Vitamin E, Essential Oils</p>
    </div>
  </section>
</div>
</body>
</html>
```